Acupuncture business needs business card design

I need a business card for an acupuncture clinic called "Harbourlight Wellness"
It will need the following details:
My name: Marcus Pelling
Acupuncturist
Member TVBH
KWF Treatment Provider
Ph numbers: 581 2734 027 418 5620
Email: marcus@hbwel.example.nz
On the back it will need a table with 2 columns for appointments, one column for time and one for date.

Industry/Entity Type

Clinic

Contact Information for Business Card

Marcus Pelling
Acupuncturist
Member TVBH
KWF Treatment Provider
Email: marcus@hbwel.example.nz

Requirements
Must have
• Marcus Pelling
• Acupuncturist
• Member TVBH
• KWF Treatment Provider
• Ph numbers: 581 2734 027 418 5620
• Email: marcus@hbwel.example.nz
• On the back it will need a table with 2 columns for appointments, one column for time and one for date.

```html
<!DOCTYPE html>
<html lang="en">
<head>
<meta charset="utf-8">
<title>Harbourlight Wellness – Business Card</title>
<link rel="stylesheet" href="https://fonts.googleapis.com/css2?family=Titillium+Web:wght@300;400;600;700&display=swap">
<style>
  :root {
    --page-bg: #e9ebec;
    --front-bg: #050505;
    --accent: #1fb8e0;
    --accent-soft: #1f8fb0;
    --muted: #8fa4ad;
    --back-bg: #137a95;
    --cell: #d7e6ea;
    --back-text: #eef6f8;
  }
  * { box-sizing: border-box; margin: 0; padding: 0; }
  html, body {
    width: 1200px; height: 948px; overflow: hidden;
    background: var(--page-bg);
    font-family: "Titillium Web", sans-serif;
  }
  .sheet {
    width: 1200px; height: 948px;
    display: flex; flex-direction: column; align-items: center;
    justify-content: center; gap: 36px;
  }
  .card {
    position: relative;
    width: 735px; height: 420px;
    box-shadow: 0 6px 18px rgba(0,0,0,.18);
    overflow: hidden;
  }

  /* Front */
  .card--front { background: var(--front-bg); color: var(--accent); }
  .brand {
    position: absolute; left: 44px; top: 40px;
    display: flex; align-items: center; gap: 14px;
  }
  .brand__dot {
    width: 40px; height: 40px; border-radius: 50%;
    background: var(--accent-soft);
  }
  .brand__name {
    font-size: 40px; font-weight: 600; line-height: 1;
    color: var(--accent); letter-spacing: .5px;
  }
  .brand__tagline {
    position: absolute; left: 98px; top: 88px;
    font-size: 12px; letter-spacing: 5.2px; font-weight: 400;
    color: var(--accent-soft); text-transform: uppercase;
  }
  .contact {
    position: absolute; left: 44px; top: 170px;
    list-style: none; font-size: 17px; color: var(--accent);
    display: flex; flex-direction: column; gap: 12px;
  }
  .contact__item { display: flex; align-items: center; gap: 10px; }
  .contact__icon { width: 16px; height: 16px; flex: none; }
  .person {
    position: absolute; right: 44px; bottom: 44px; text-align: right;
  }
  .person__name { font-size: 26px; font-weight: 700; color: var(--accent); line-height: 1.2; }
  .person__role { font-size: 15px; color: var(--accent-soft); line-height: 1.35; }

  /* Back */
  .card--back { background: var(--back-bg); color: var(--back-text); }
  .appointments {
    position: absolute; left: 70px; top: 50px;
    border-collapse: separate; border-spacing: 16px 14px;
  }
  .appointments th {
    text-align: left; font-weight: 400; font-size: 20px;
    letter-spacing: 1px; padding-left: 2px;
  }
  .appointments td {
    width: 270px; height: 40px; background: var(--cell);
  }
  .website {
    position: absolute; left: 0; right: 0; bottom: 34px;
    text-align: center; font-size: 22px; letter-spacing: 4px;
  }
</style>
</head>
<body>
<main class="sheet">
  <section class="card card--front" aria-label="Business card front">
    <div class="brand">
      <span class="brand__dot"></span>
      <span class="brand__name">Harbourlight Wellness</span>
    </div>
    <p class="brand__tagline">Acupuncture Physiotherapy</p>

    <ul class="contact">
      <li class="contact__item">
        <svg class="contact__icon" viewBox="0 0 16 16" aria-hidden="true">
          <circle cx="8" cy="8" r="8" fill="var(--accent)"/>
          <path d="M5.3 4.2l1.4 1.6-.8 1c.6 1.2 1.4 2 2.6 2.6l1-.8 1.6 1.4-.9 1.4c-2.9-.4-5.2-2.7-5.6-5.6z" fill="var(--front-bg)"/>
        </svg>
        <span>581 2734 · 027 418 5620</span>
      </li>
      <li class="contact__item">
        <svg class="contact__icon" viewBox="0 0 16 16" aria-hidden="true">
          <rect x="0" y="2" width="16" height="12" rx="2" fill="var(--accent)"/>
          <path d="M2 4.5l6 4.5 6-4.5" stroke="var(--front-bg)" stroke-width="1.5" fill="none"/>
        </svg>
        <span>marcus@hbwel.example.nz</span>
      </li>
    </ul>

    <div class="person">
      <p class="person__name">Marcus Pelling</p>
      <p class="person__role">Acupuncturist Member TVBH</p>
      <p class="person__role">KWF Treatment Provider</p>
    </div>
  </section>

  <section class="card card--back" aria-label="Business card back">
    <table class="appointments">
      <thead>
        <tr><th scope="col">Date</th><th scope="col">Time</th></tr>
      </thead>
      <tbody>
        <tr><td></td><td></td></tr>
        <tr><td></td><td></td></tr>
        <tr><td></td><td></td></tr>
        <tr><td></td><td></td></tr>
      </tbody>
    </table>
    <p class="website">www.hbwel.example.nz</p>
  </section>
</main>
</body>
</html>
```